New website for engineering consultant

We need to update our existing web site. We've just had our logo re-done and have attached it.

We are an engineering consulting firm that specialises in mechanical and structural engineering, design and drafting. Our customers are other businesses in the manufacturing, mining and agricultural industries.

We would like the designs to be professional and highlight that we are innovative.

Industry/Entity Type

Mining

Requirements
Must have
• A module that rotates pictures so we can showcase certain projects. We have attached a few rendered images of projects for you to play with.

```html
<!DOCTYPE html>
<html lang="en">
<head>
<meta charset="utf-8">
<title>KORVEN-MECH — Engineering Sustainable</title>
<link href="https://fonts.googleapis.com/css2?family=Ubuntu:wght@400;500;700&display=swap" rel="stylesheet">
<style>
:root{
  --page-bg:#2b2d31;
  --white:#ffffff;
  --nav:#0633a3;
  --nav-line:#3a5fc0;
  --heading:#1a3a9c;
  --body-blue:#1f3fa6;
  --grey-text:#6b6b6b;
  --dark-text:#222222;
  --bar-grey:#f0f0f0;
  --footer:#0b1f6e;
  --tile-border:#d4d4d4;
}
*{margin:0;padding:0;box-sizing:border-box}
html,body{width:1034px;height:1200px;overflow:hidden}
body{
  position:relative;
  font-family:"Ubuntu",Arial,sans-serif;
  background:linear-gradient(180deg,#1e2024 0,#4a4c50 120px,#3a3c40 400px,var(--page-bg) 1200px);
}
.page{position:absolute;left:14px;top:22px;width:992px;height:1099px;background:var(--white);border-radius:4px 4px 0 0}
.header{position:absolute;left:0;top:0;width:992px;height:131px;background:linear-gradient(180deg,#ffffff,#efefef);border-radius:4px 4px 0 0;border-bottom:2px solid #c9c9c9}
.brand{position:absolute;left:22px;top:52px;display:flex;align-items:center;gap:12px}
.brand-dot{width:34px;height:34px;border-radius:50%;background:var(--heading)}
.brand-name{font-size:30px;font-weight:700;color:var(--heading);letter-spacing:0.5px;white-space:nowrap}
.search{position:absolute;left:720px;top:78px;width:257px;height:28px;border:1px solid #c8c8c8;border-radius:6px;background:#fff;box-shadow:0 2px 3px rgba(0,0,0,.12)}
.search span{position:absolute;left:8px;top:6px;font-size:13px;font-style:italic;color:#555;white-space:nowrap}
.search .btn{position:absolute;right:0;top:0;width:30px;height:26px;border-left:1px solid #ddd;background:#f4f4f4;border-radius:0 6px 6px 0}
.search svg{position:absolute;left:6px;top:4px}
.nav{position:absolute;left:0;top:133px;width:992px;height:46px;background:var(--nav);display:flex}
.nav a{flex:none;display:block;color:#fff;text-decoration:none;font-size:14px;line-height:46px;text-align:center;white-space:nowrap;border-right:1px solid var(--nav-line)}
.nav a:last-child{border-right:none}
.hero{position:absolute;left:0;top:179px;width:992px;height:310px;background:linear-gradient(90deg,#dde9fb 0,#9fc1f0 30%,#d9e6f6 50%,#f3f4f6 70%,#e8e4df 100%)}
.hero-card{position:absolute;left:20px;top:78px;width:438px;height:89px;background:#fff;padding:14px 16px}
.hero-card h1{font-size:21px;font-weight:500;color:#1a2f78;white-space:nowrap;letter-spacing:-0.2px}
.hero-card p{font-size:18px;color:#1a2f78;margin-top:8px;white-space:nowrap}
.welcome{position:absolute;left:20px;top:508px;width:664px}
.welcome h2{font-size:18px;font-weight:400;color:var(--heading);margin-bottom:10px;white-space:nowrap}
.welcome p{font-size:11px;line-height:17px;color:var(--body-blue);margin-bottom:17px}
.section-bar{position:absolute;left:16px;top:727px;width:668px;height:34px;border-radius:5px;background:linear-gradient(180deg,#cfe2fb,#9cc3f1);padding:8px 17px;font-size:15px;color:var(--heading)}
.tile{position:absolute;width:213px;height:120px;border:1px solid var(--tile-border);box-shadow:0 1px 3px rgba(0,0,0,.12);background:#fff;padding:4px}
.tile div{width:100%;height:100%}
.more-bar{position:absolute;top:1050px;height:25px;background:var(--bar-grey);font-size:12.5px;color:var(--dark-text);padding:5px 12px;white-space:nowrap}
.divider{position:absolute;left:704px;top:508px;width:1px;height:532px;background:#dcdcdc}
.news-title{position:absolute;left:723px;top:508px;font-size:18px;font-weight:400;color:var(--heading);white-space:nowrap}
.news{position:absolute;left:723px;width:255px}
.news .thumb{position:absolute;left:0;top:0;width:82px;height:75px;border:2px solid #8aa7d9}
.news .date{position:absolute;left:95px;top:2px;font-size:12.5px;color:var(--dark-text);white-space:nowrap}
.news .lead{position:absolute;left:95px;top:22px;width:160px;font-size:11px;line-height:17px;color:var(--grey-text)}
.news .body{position:absolute;left:0;top:82px;width:240px;font-size:11px;line-height:17px;color:var(--grey-text)}
.news .read{position:absolute;left:0;font-size:12px;color:var(--dark-text);white-space:nowrap}
.footer{position:absolute;left:0;top:1121px;width:1034px;height:79px;background:var(--footer);color:#fff;font-size:11px}
.footer .copy{position:absolute;left:20px;top:17px;white-space:nowrap}
.footer .links{position:absolute;right:46px;top:17px;display:flex;white-space:nowrap}
.footer .links a{color:#fff;text-decoration:none}
.footer .links i{font-style:normal;margin:0 8px}
</style>
</head>
<body>
<div class="page">
  <header class="header">
    <div class="brand"><span class="brand-dot"></span><span class="brand-name">KORVEN-MECH</span></div>
    <div class="search"><span>Search here..</span><div class="btn"><svg width="18" height="18" viewBox="0 0 18 18"><circle cx="7" cy="7" r="5" fill="none" stroke="#111" stroke-width="2"/><line x1="11" y1="11" x2="16" y2="16" stroke="#111" stroke-width="2.5" stroke-linecap="round"/></svg></div></div>
  </header>
  <nav class="nav">
    <a href="#" style="width:87px">Home</a><a href="#" style="width:92px">About Us</a><a href="#" style="width:171px">Engineering &amp; Design</a><a href="#" style="width:106px">Technology</a><a href="#" style="width:179px">Improvement Services</a><a href="#" style="width:146px">Speciality Services</a><a href="#" style="width:87px">Projects</a><a href="#" style="width:124px">Contact Us</a>
  </nav>
  <section class="hero" role="img" aria-label="Engineer in safety glasses examining a sample beside blue gear technical drawings">
    <div class="hero-card"><h1>KORVEN-MECH Engineering Sustainable</h1><p>Your tittle line goes here..</p></div>
  </section>

  <section class="welcome">
    <h2>Welcome To Our Website Main Page</h2>
    <p>KORVEN-MECH is a mechanical engineering and technology company focused on helping local manufacturing companies and local industries improve their products, services and sustainability through the application of engineering, technology and focused improvement.</p>
    <p>We offer a broad range of services that are designed to support and nurture manufacturing companies and industries whether you are big or small. We bring togther the services you would only find in a capital city to companies in North Queensland at a competitive rates. Our core services revolve around the application of the latest 3D Solid Modelling technology to assist in creating solutions to your mechanical design problems. These services are complemented by our Technology services which are designed to help your company leverage the latest technology to become globally competitive. Furthermore we offer a range of Focused Improvement and Specialty services as we strive to bring you complete solutions to your business.</p>
  </section>

  <div class="section-bar">Our Equipments</div>
  <div class="tile" style="left:19px;top:773px"><div role="img" aria-label="Yellow moulded part render" style="background:linear-gradient(135deg,#fafafa,#e8e27a 50%,#f7f7f7)"></div></div>
  <div class="tile" style="left:243px;top:773px"><div role="img" aria-label="Steel frame structure render" style="background:linear-gradient(135deg,#fbfbfb,#bdbdbd 50%,#fbfbfb)"></div></div>
  <div class="tile" style="left:469px;top:773px"><div role="img" aria-label="Vehicle bull bar render" style="background:linear-gradient(135deg,#f7f7f7,#8c8c8c 55%,#f2f2f2)"></div></div>
  <div class="tile" style="left:20px;top:908px"><div role="img" aria-label="Elevated platform with stairs render" style="background:linear-gradient(135deg,#fbfbfb,#9a9aae 50%,#f5f5e6)"></div></div>
  <div class="tile" style="left:245px;top:908px"><div role="img" aria-label="Reel storage rack render" style="background:linear-gradient(135deg,#fbfbfb,#c4c4c4 50%,#fbfbfb)"></div></div>
  <div class="tile" style="left:470px;top:908px"><div role="img" aria-label="Covered platform structure render" style="background:linear-gradient(135deg,#fbfbfb,#6d6fb8 45%,#f4f4e4)"></div></div>
  <div class="more-bar" style="left:16px;width:670px">VIEW ALL &#8250;</div>

  <div class="divider"></div>
  <h3 class="news-title">Latest News &amp; Projects</h3>

  <article class="news" style="top:541px">
    <div class="thumb" role="img" aria-label="Workshop test equipment photo" style="background:linear-gradient(135deg,#f0d79a,#8c8f96)"></div>
    <div class="date">20.March.2012</div>
    <p class="lead">It's the simplest, cheapest and also the basic thing the search engine picks it up very easily.</p>
    <p class="body">We at Brightline tech provide you the best simple websites too with total work done as using all the best designing and all done</p>
    <div class="read" style="top:142px">READ MORE &#8250;</div>
  </article>
  <article class="news" style="top:714px">
    <div class="thumb" role="img" aria-label="Technician working on a machine photo" style="background:linear-gradient(135deg,#9a9a9a,#3c3c3c)"></div>
    <div class="date">20.March.2012</div>
    <p class="lead">It's the simplest, cheapest and also the basic thing the search engine picks it up very easily.</p>
    <p class="body">We at Brightline tech provide you the best simple websites too with total work done as using all the best designing and all done</p>
    <div class="read" style="top:142px">READ MORE &#8250;</div>
  </article>
  <article class="news" style="top:891px;left:726px">
    <div class="thumb" role="img" aria-label="Vintage lathe machinery photo" style="background:linear-gradient(135deg,#b08a5a,#5b4632)"></div>
    <div class="date">20.March.2012</div>
    <p class="lead">It's the simplest, cheapest and also the basic thing the search engine picks it up very easily.</p>
    <p class="body">We at Brightline tech provide you the best simple websites too</p>
    <div class="read" style="top:122px">READ MORE &#8250;</div>
  </article>
  <div class="more-bar" style="left:724px;width:254px">READ ALL &#8250;</div>
</div>

<footer class="footer">
  <div class="copy">© 2012 Company Name &nbsp;|&nbsp; All right reserved</div>
  <div class="links">
    <a href="#">Home</a><i>|</i><a href="#">About Us</a><i>|</i><a href="#">Engineering &amp; Design</a><i>|</i><a href="#">Technology</a><i>|</i><a href="#">Improvement Services</a><i>|</i><a href="#">Speciality Services</a><i>|</i><a href="#">Projects</a><i>|</i><a href="#">Contact Us</a>
  </div>
</footer>
</body>
</html>
```